BrindleStaffing Business Card Design

We are a staffing company finding positions for dedicated nurses and physicians.

Target Market(s)

Business Professionals

Industry/Entity Type

Staffing

Contact Information for Business Card

Gordon Pratley
Chairman
417 39th Avenue South
SAINT PETERSBURG FL 33712
813-555-4172 Mobile
813-555-8036 Fax
gpratley@brindlestaffing.com
www.brindlestaffing.com

Font styles to use
Sans Serif

Colors
fbee3e
f04a50
f37122

Requirements
Must have
• Logo Attached, see colors below. We'd like to see Yellow, Orange and Red.

```html
<!DOCTYPE html>
<html lang="en">
<head>
<meta charset="utf-8">
<title>BrindleStaffing Business Card</title>
<link href="https://fonts.googleapis.com/css2?family=Rubik:wght@400;500;700&display=swap" rel="stylesheet">
<style>
  :root {
    --bg: #e9e9eb;
    --red: #f04a50;
    --orange: #f37122;
    --yellow: #fbee3e;
    --ink: #1c1c1c;
    --white: #ffffff;
  }
  * { margin: 0; padding: 0; box-sizing: border-box; }
  html, body {
    width: 1200px; height: 1000px; overflow: hidden;
    background: var(--bg);
    font-family: "Rubik", Arial, sans-serif;
  }
  .stage { position: relative; width: 1200px; height: 1000px; }
  .card {
    position: absolute; left: 320px;
    width: 560px; height: 320px;
    box-shadow: 0 10px 30px rgba(0,0,0,0.18);
    overflow: hidden;
  }
  .card-back {
    top: 140px;
    background: linear-gradient(90deg, var(--red) 0%, var(--orange) 100%);
  }
  .card-back .brand {
    position: absolute; right: 36px; bottom: 46px;
    font-size: 34px; font-weight: 700; color: var(--white);
    letter-spacing: -0.5px;
  }
  .card-front { top: 540px; background: var(--white); }
  .card-front .brand {
    position: absolute; top: 62px; left: 0; right: 0;
    text-align: center;
    font-size: 46px; font-weight: 700; color: var(--orange);
    letter-spacing: -1px;
  }
  .identity {
    position: absolute; right: 318px; top: 190px;
    text-align: right;
  }
  .identity .person-name {
    font-size: 21px; font-weight: 700; color: var(--orange);
  }
  .identity .person-role {
    font-size: 13px; color: var(--ink); margin-top: 3px;
  }
  .divider {
    position: absolute; left: 256px; top: 160px;
    width: 1.5px; height: 86px; background: var(--red);
  }
  .contacts {
    position: absolute; left: 270px; top: 160px;
    list-style: none;
    font-size: 12.5px; color: var(--ink);
  }
  .contacts li {
    display: flex; align-items: center; gap: 8px;
    height: 19px;
  }
  .contacts svg { width: 11px; height: 11px; fill: var(--red); flex: none; }
  .contacts .accent { color: var(--red); font-weight: 500; }
  .address-band {
    position: absolute; left: 0; right: 0; bottom: 0;
    height: 44px; background: var(--red);
    color: var(--white); font-size: 12px; font-weight: 500;
    display: flex; align-items: center; justify-content: center;
    letter-spacing: 0.2px;
  }
</style>
</head>
<body>
<main class="stage">
  <section class="card card-back" aria-label="Card back">
    <div class="brand">BrindleStaffing</div>
  </section>

  <section class="card card-front" aria-label="Card front">
    <div class="brand">BrindleStaffing</div>

    <div class="identity">
      <div class="person-name">Gordon Pratley</div>
      <div class="person-role">Chairman</div>
    </div>

    <div class="divider"></div>

    <ul class="contacts">
      <li>
        <svg viewBox="0 0 24 24" aria-hidden="true"><path d="M6.6 10.8a15.1 15.1 0 0 0 6.6 6.6l2.2-2.2a1 1 0 0 1 1-.25 11.4 11.4 0 0 0 3.6.57 1 1 0 0 1 1 1V20a1 1 0 0 1-1 1A17 17 0 0 1 3 4a1 1 0 0 1 1-1h3.5a1 1 0 0 1 1 1c0 1.25.2 2.45.57 3.6a1 1 0 0 1-.25 1z"/></svg>
        813-555-4172
      </li>
      <li>
        <svg viewBox="0 0 24 24" aria-hidden="true"><path d="M6 2h10v5H6zM3 9h18a1 1 0 0 1 1 1v8h-4v4H6v-4H2v-8a1 1 0 0 1 1-1zm5 7v4h8v-4z"/></svg>
        813-555-8036
      </li>
      <li>
        <svg viewBox="0 0 24 24" aria-hidden="true"><path d="M2 5h20v14H2zm2 2v.5l8 5 8-5V7l-8 5z"/></svg>
        gpratley@brindlestaffing.com
      </li>
      <li>
        <svg viewBox="0 0 24 24" aria-hidden="true"><path d="M12 2a10 10 0 1 0 0 20 10 10 0 0 0 0-20zm6.9 9h-3a15 15 0 0 0-1.3-6A8 8 0 0 1 18.9 11zM12 4.1A13 13 0 0 1 13.9 11h-3.8A13 13 0 0 1 12 4.1zM9.4 5a15 15 0 0 0-1.3 6h-3A8 8 0 0 1 9.4 5zM5.1 13h3a15 15 0 0 0 1.3 6A8 8 0 0 1 5.1 13zm6.9 6.9A13 13 0 0 1 10.1 13h3.8A13 13 0 0 1 12 19.9zm2.6-.9a15 15 0 0 0 1.3-6h3a8 8 0 0 1-4.3 6z"/></svg>
        <span>www.<span class="accent">brindlestaffing</span>.com</span>
      </li>
    </ul>

    <div class="address-band">417 39th Avenue South SAINT PETERSBURG FL 33712</div>
  </section>
</main>
</body>
</html>
```